Residential Remodeling Contractor needs updated business card

I need a new design for my business card.
Name of the company is Ridgefell Construction. I need a card that commands presence, strength, integrity. I have been in business for 28 years. I am a Residential Remodeling Contractor that covers all aspects of a residential remodel and build.

```html
<!DOCTYPE html>
<html lang="en">
<head>
<meta charset="utf-8">
<title>Ridgefell Construction – Business Card</title>
<link href="https://fonts.googleapis.com/css2?family=Montserrat:wght@400;500;600;700&display=swap" rel="stylesheet">
<style>
  :root {
    --card-blue: #1f3d80;
    --card-blue-deep: #1b3673;
    --ink-navy: #0f1d3d;
    --paper: #ffffff;
    --stage: #d9dbdf;
  }
  * { margin: 0; padding: 0; box-sizing: border-box; }
  html, body { width: 1200px; height: 900px; overflow: hidden; }
  body {
    background: var(--stage);
    font-family: "Montserrat", Arial, sans-serif;
    display: flex;
    flex-direction: column;
    align-items: center;
    justify-content: center;
    gap: 40px;
  }
  .card {
    position: relative;
    width: 700px;
    height: 400px;
    background: var(--card-blue);
    overflow: hidden;
    box-shadow: 0 10px 24px rgba(0,0,0,0.25);
  }

  /* Back side */
  .card-back { display: flex; flex-direction: column; align-items: center; justify-content: center; }
  .card-back .wordmark {
    color: var(--ink-navy);
    font-weight: 600;
    font-size: 38px;
    letter-spacing: 3px;
    line-height: 1.1;
    text-transform: uppercase;
    text-align: center;
    display: flex;
    align-items: center;
    gap: 18px;
  }
  .wordmark-square { width: 22px; height: 22px; background: currentColor; flex: none; }
  .card-back .tagline {
    margin-top: 70px;
    color: var(--paper);
    font-weight: 500;
    font-size: 14px;
    letter-spacing: 1.5px;
    text-transform: uppercase;
  }

  /* Front side */
  .card-front .wordmark {
    position: absolute;
    left: 60px;
    top: 56px;
    color: var(--paper);
    font-weight: 600;
    font-size: 28px;
    letter-spacing: 2px;
    line-height: 1.15;
    text-transform: uppercase;
    display: flex;
    align-items: center;
    gap: 16px;
  }
  .card-front .wordmark-square { width: 18px; height: 18px; }
  .holder {
    position: absolute;
    right: 72px;
    top: 170px;
    text-align: right;
    color: var(--paper);
  }
  .holder-name { font-weight: 700; font-size: 28px; letter-spacing: 2px; text-transform: uppercase; }
  .holder-role { font-weight: 500; font-size: 16px; letter-spacing: 1px; margin-top: 4px; }
  .edge-tab {
    position: absolute;
    right: 0;
    top: 198px;
    width: 30px;
    height: 42px;
    background: var(--paper);
    border-radius: 8px 0 0 8px;
  }
  .contacts {
    position: absolute;
    left: 60px;
    bottom: 50px;
    color: var(--paper);
    list-style: none;
    font-size: 18px;
    font-weight: 400;
    line-height: 1.35;
    letter-spacing: 0.5px;
  }
  .contacts li { display: flex; align-items: center; gap: 6px; }
  .contacts svg { width: 14px; height: 14px; flex: none; }
  .contacts .address { margin-top: 6px; }
</style>
</head>
<body>

  <section class="card card-back">
    <div class="wordmark"><span class="wordmark-square"></span><span>Ridgefell<br>Construction</span></div>
    <p class="tagline">I have been in business for 28 years</p>
  </section>

  <section class="card card-front">
    <div class="wordmark"><span class="wordmark-square"></span><span>Ridgefell<br>Construction</span></div>

    <div class="holder">
      <div class="holder-name">Marcus Thorne</div>
      <div class="holder-role">Director</div>
    </div>
    <div class="edge-tab"></div>

    <ul class="contacts">
      <li>
        <svg viewBox="0 0 16 16" fill="none" stroke="#fff" stroke-width="1.6"><path d="M4 1.5h2.5l1 3.5-1.8 1.2a8 8 0 0 0 4.1 4.1L11 8.5l3.5 1V12c0 1-1 2-2 2C6.5 14 2 9.5 2 3.5c0-1 1-2 2-2z"/></svg>
        (555) 014-2290
      </li>
      <li>
        <svg viewBox="0 0 16 16" fill="none" stroke="#fff" stroke-width="1.4"><rect x="1.5" y="3.5" width="13" height="9"/><path d="M1.5 3.5 8 9l6.5-5.5"/></svg>
        info@ridgefellconstru.com
      </li>
      <li>
        <svg viewBox="0 0 16 16" fill="none" stroke="#fff" stroke-width="1.3"><circle cx="8" cy="8" r="6.5"/><ellipse cx="8" cy="8" rx="3" ry="6.5"/><path d="M1.5 8h13M2.5 4.8h11M2.5 11.2h11"/></svg>
        www.ridgefellconstru.com
      </li>
      <li class="address">212 Harlow Street Millbrook, GA 30100</li>
    </ul>
  </section>

</body>
</html>
```